UX - Need some screens design for a Skill Assessment Application

I am building an app to carry out skill assessments. Depending on how the assessment is configured, it may have one or more parts
1. Question based assessment (Multiple Choice, True False, Fill in the blanks"
2. Endorsement by two colleagues - A screen that allows user to pick colleagues based on search and shows the status of pending requests
3. A written submission - a page that explains the format of the submission and a file upload
As each assessment can be configured with or without any of the steps, the assessment UI must be such that these areas get hidden/displayed based on configuration.
Colour codes to be used can be #0e78bb and #ffffff
There will also be a start screen (instructions) and an end screen (results)
Target Market(s)
Enterprise software
Number of Pages Required
4 page

```html
<!DOCTYPE html>
<html lang="en">
<head>
<meta charset="utf-8">
<title>Application Design Capabilities – Quiz</title>
<link href="https://fonts.googleapis.com/css2?family=Inter:wght@400;500;600;700&display=swap" rel="stylesheet">
<style>
:root{
  --brand:#0e78bb;
  --header:#0a56ab;
  --accent:#2bb3e6;
  --white:#ffffff;
  --ink:#1e1f22;
  --muted:#5f6368;
  --faint:#9aa0a6;
  --line:#dfe2e6;
  --band:#f5f6f8;
  --chip:#e8eaed;
  --num:#cdeaf7;
  --teal:#12939a;
}
*{box-sizing:border-box;margin:0;padding:0}
html,body{width:1200px;height:771px;overflow:hidden;background:var(--white);font-family:"Inter",sans-serif;color:var(--ink)}
.canvas{position:relative;width:1200px;height:771px}
.abs{position:absolute}
.topbar{left:0;top:0;width:1200px;height:43px;background:var(--header)}
.brand{left:71px;top:11px;display:flex;align-items:center;gap:10px;color:var(--white);font-size:14px;font-weight:600}
.brand-dot{width:20px;height:20px;border-radius:50%;background:var(--accent)}
.nav{top:14px;font-size:12.5px;color:#d4e4f5}
.nav.active{color:var(--white);font-weight:600}
.nav-underline{left:487px;top:41px;width:80px;height:2px;background:var(--accent)}
.avatar{left:1100px;top:9px;width:27px;height:27px;border-radius:50%;background:linear-gradient(135deg,#6b86a6,#2d3a4e)}
.crumb{top:67px;font-size:11.5px;color:var(--muted)}
.crumb a{color:var(--brand);text-decoration:none}
.title{left:122px;top:98px;font-size:21px;font-weight:600;letter-spacing:-.1px}
.updated{right:90px;top:112px;font-size:11px;color:var(--muted)}
.updated b{font-weight:500;color:var(--ink)}
.meta-band{left:0;top:140px;width:1200px;height:45px;background:var(--band);border-top:1px solid var(--line);border-bottom:1px solid var(--line)}
.meta{top:156px;font-size:10.5px;color:var(--ink)}
.meta .v{color:var(--brand)}
.meta .g{color:var(--muted)}
.meta-sep{top:155px;width:1px;height:15px;background:var(--line)}
.chip{top:151px;height:23px;border-radius:12px;background:var(--chip);font-size:11.5px;color:var(--muted);display:flex;align-items:center;justify-content:center}
.step{left:88px;width:214px;height:43px;border:1px solid var(--line);border-radius:3px;font-size:12px;color:var(--faint);padding-left:17px;display:flex;align-items:center}
.step.current{border:1.5px solid var(--brand);color:var(--ink)}
.section-h{left:365px;top:219px;font-size:15px;font-weight:700}
.btn-outline{border:1px solid var(--brand);color:var(--brand);background:var(--white);border-radius:2px;font-size:11.5px;font-weight:500;display:flex;align-items:center;justify-content:center}
.btn-solid{background:var(--brand);color:var(--white);border-radius:2px;font-size:11.5px;font-weight:500;display:flex;align-items:center;justify-content:center}
.rule{left:365px;top:254px;width:745px;height:1px;background:var(--line)}
.qno{left:366px;top:272px;font-size:15px;color:var(--muted)}
.qtext{left:416px;top:271px;font-size:15.5px;font-weight:500}
.row{left:365px;width:468px;height:58px;border:1px solid var(--line);border-radius:2px}
.row .num{position:absolute;left:13px;top:14px;width:31px;height:27px;background:var(--num);color:var(--muted);font-size:13px;display:flex;align-items:center;justify-content:center}
.row .txt{position:absolute;left:64px;top:19px;font-size:12px;color:var(--muted)}
.pill{position:absolute;top:13px;height:31px;border-radius:16px;font-size:11.5px;font-weight:500;display:flex;align-items:center;justify-content:center}
.pill.on{background:var(--brand);color:var(--white)}
.pill.off{border:1px solid var(--line);color:var(--brand);background:var(--white)}
.pill.t{left:340px;width:51px}
.pill.f{left:398px;width:55px}
.progress-label{left:908px;top:281px;font-size:12px;color:var(--muted)}
.progress-count{left:1087px;top:282px;font-size:10px;color:var(--muted)}
.progress-count b{color:var(--ink)}
.note{left:896px;top:325px;width:214px;height:129px;background:var(--band);border-radius:4px;padding:20px 20px}
.note h3{font-size:15px;font-weight:500;margin-bottom:10px}
.note p{font-size:12px;line-height:20.5px;color:var(--muted)}
.pct{left:88px;top:662px;font-size:27px;font-weight:700;letter-spacing:-.5px}
.pct small{font-size:13px;font-weight:500;margin-left:2px}
.track{left:0;top:702px;width:1200px;height:6px;background:#eef0f2}
.fill{left:0;top:702px;width:342px;height:6px;background:var(--teal)}
.skip{left:998px;top:731px;font-size:11.5px;color:var(--muted);display:flex;align-items:center;gap:4px}
</style>
</head>
<body>
<div class="canvas">
  <header class="abs topbar"></header>
  <div class="abs brand"><span class="brand-dot"></span>Quenvale</div>
  <span class="abs nav active" style="left:487px">Assessments</span>
  <div class="abs nav-underline"></div>
  <span class="abs nav" style="left:587px">Colleagues</span>
  <span class="abs nav" style="left:670px">Results</span>
  <svg class="abs" style="left:1027px;top:12px" width="18" height="20" viewBox="0 0 18 20" fill="none" stroke="#fff" stroke-width="1.4"><path d="M3 14V8a6 6 0 0 1 12 0v6l1.5 2h-15z"/><path d="M7 18a2 2 0 0 0 4 0"/></svg>
  <svg class="abs" style="left:1062px;top:13px" width="18" height="18" viewBox="0 0 24 24" fill="none" stroke="#fff" stroke-width="1.6"><circle cx="12" cy="12" r="3"/><path d="M19.4 15a1.7 1.7 0 0 0 .3 1.8l.1.1a2 2 0 1 1-2.8 2.8l-.1-.1a1.7 1.7 0 0 0-1.8-.3 1.7 1.7 0 0 0-1 1.5V21a2 2 0 0 1-4 0v-.1a1.7 1.7 0 0 0-1.1-1.5 1.7 1.7 0 0 0-1.8.3l-.1.1a2 2 0 1 1-2.8-2.8l.1-.1a1.7 1.7 0 0 0 .3-1.8 1.7 1.7 0 0 0-1.5-1H3a2 2 0 0 1 0-4h.1a1.7 1.7 0 0 0 1.5-1.1 1.7 1.7 0 0 0-.3-1.8l-.1-.1a2 2 0 1 1 2.8-2.8l.1.1a1.7 1.7 0 0 0 1.8.3H9a1.7 1.7 0 0 0 1-1.5V3a2 2 0 0 1 4 0v.1a1.7 1.7 0 0 0 1 1.5 1.7 1.7 0 0 0 1.8-.3l.1-.1a2 2 0 1 1 2.8 2.8l-.1.1a1.7 1.7 0 0 0-.3 1.8V9a1.7 1.7 0 0 0 1.5 1H21a2 2 0 0 1 0 4h-.1a1.7 1.7 0 0 0-1.5 1z"/></svg>
  <div class="abs avatar" role="img" aria-label="User profile photo"></div>

  <svg class="abs" style="left:56px;top:65px" width="20" height="20" viewBox="0 0 20 20" fill="none" stroke="#0e78bb" stroke-width="1.6"><circle cx="10" cy="10" r="9"/><path d="M14 10H6M9.5 6.5 6 10l3.5 3.5"/></svg>
  <div class="abs crumb" style="left:88px"><a href="#">Assessment</a>&nbsp;&nbsp;/&nbsp;&nbsp;Application Design Capabilities</div>

  <svg class="abs" style="left:88px;top:101px" width="22" height="22" viewBox="0 0 22 22" fill="none" stroke="#5f6368" stroke-width="1.4"><path d="M15 8V2H2v18h8"/><path d="M5 6h7M5 10h4M5 14h3"/><circle cx="15" cy="15" r="4.5"/><path d="M13 15l1.5 1.5L17 14M18.5 18.5 21 21"/></svg>
  <h1 class="abs title">Application Design Capabilities</h1>
  <div class="abs updated">Last Updated: <b>23/05/2024</b></div>

  <div class="abs meta-band"></div>
  <div class="abs meta" style="left:88px">Assessment Date: <span class="v">May 20, 2024</span></div>
  <div class="abs meta-sep" style="left:267px"></div>
  <div class="abs meta" style="left:288px">Assessment Type: <span class="v">UI/UX Skill</span></div>
  <div class="abs meta-sep" style="left:451px"></div>
  <div class="abs meta" style="left:473px">Due Date: <span class="g">24/05/2024</span></div>
  <div class="abs chip" style="left:888px;width:41px">Quiz</div>
  <div class="abs chip" style="left:936px;width:88px">Endorsement</div>
  <div class="abs chip" style="left:1031px;width:79px">Submission</div>

  <div class="abs step current" style="top:219px">Quiz</div>
  <div class="abs step" style="top:271px">Endorsement</div>
  <div class="abs step" style="top:322px">Submission</div>

  <h2 class="abs section-h">Quiz</h2>
  <div class="abs btn-outline" style="left:1006px;top:213px;width:104px;height:31px">Save Progress</div>
  <div class="abs rule"></div>

  <div class="abs qno">Q.6.</div>
  <div class="abs qtext">This is multiple question with T/F choice</div>

  <div class="abs row" style="top:317px"><span class="num">1</span><span class="txt">Lorem ipsum dolor sit amet?</span><span class="pill on t">True</span><span class="pill off f">False</span></div>
  <div class="abs row" style="top:382px"><span class="num">2</span><span class="txt">Lorem ipsum dolor sit amet?</span><span class="pill off t">True</span><span class="pill on f">False</span></div>
  <div class="abs row" style="top:447px"><span class="num">3</span><span class="txt">Lorem ipsum dolor sit amet?</span><span class="pill on t">True</span><span class="pill off f">False</span></div>

  <svg class="abs" style="left:894px;top:283px" width="8" height="10" viewBox="0 0 8 10" fill="none" stroke="#5f6368" stroke-width="1.4"><path d="M2 1l4 4-4 4"/></svg>
  <div class="abs progress-label">Progress</div>
  <svg class="abs" style="left:1050px;top:272px" width="31" height="31" viewBox="0 0 31 31" fill="none" stroke-width="3"><circle cx="15.5" cy="15.5" r="13.5" stroke="#e3f3fa"/><circle cx="15.5" cy="15.5" r="13.5" stroke="#2bb3e6" stroke-dasharray="63.6 84.8" transform="rotate(-90 15.5 15.5)"/></svg>
  <div class="abs progress-count"><b>6</b> / 8</div>

  <aside class="abs note">
    <h3>Note</h3>
    <p>Lorem ipsum dolor sit amet, consecteteur adispiscing elit. Lorem ipsum dolor sit amet</p>
  </aside>

  <div class="abs pct">27<small>%</small></div>
  <div class="abs track"></div>
  <div class="abs fill"></div>

  <div class="abs btn-outline" style="left:88px;top:722px;width:72px;height:31px">Go Back</div>
  <div class="abs skip">Skip <svg width="7" height="9" viewBox="0 0 7 9" fill="none" stroke="#1e1f22" stroke-width="1.4"><path d="M1.5 1l3.5 3.5L1.5 8"/></svg></div>
  <div class="abs btn-solid" style="left:1058px;top:722px;width:52px;height:31px">Next</div>
</div>
</body>
</html>
```